Local fast-growing company in the service sector

We are looking for a modern business card design, which should also appear on our letterheads

Target Market(s)

Private and industrial sectors

Contact Information for Business Card

Vorname Name
Kellberger Str. 18
74589 Lindenhain
Tel.: 07146-839214-0
Name@agentur-kvtl.de

Colors
9d9d9d
919191
aaaaaa

Requirements
Must have
• The logo (file) in silver

```html
<!DOCTYPE html>
<html lang="de">
<head>
<meta charset="utf-8">
<title>KVTL – Visitenkarte</title>
<link rel="stylesheet" href="https://fonts.googleapis.com/css2?family=Lato:wght@400;900&display=swap">
<style>
  :root {
    --page-bg: #e4e2df;
    --card-top: #d9d8d6;
    --card-mid: #c4c3c1;
    --card-low: #9d9d9d;
    --silver: #aaaaaa;
    --ink: #3a3a3a;
    --ink-soft: #4a4a4a;
    --chevron-line: #262626;
    --rule: #e8e8e8;
    --band: #4b4a4a;
    --band-text: #dcdcdc;
  }
  * { margin: 0; padding: 0; box-sizing: border-box; }
  html, body {
    width: 970px; height: 1200px; overflow: hidden;
    background: var(--page-bg);
    font-family: "Lato", sans-serif;
  }
  .business-card {
    position: absolute; left: 185px; top: 72px;
    width: 600px; height: 1056px;
    border-radius: 30px; overflow: hidden;
    background: linear-gradient(180deg, var(--card-top) 0%, var(--card-mid) 55%, var(--card-low) 100%);
    box-shadow: 0 10px 30px rgba(0,0,0,0.18), inset 0 0 0 1px rgba(255,255,255,0.6);
  }
  .card-shape { position: absolute; inset: 0; }
  .brand {
    position: absolute; left: 0; right: 0; top: 270px;
    display: flex; flex-direction: column; align-items: center;
  }
  .brand-name-row { display: flex; align-items: center; gap: 22px; }
  .brand-mark { width: 62px; height: 62px; background: var(--silver); }
  .brand-name {
    font-weight: 900; font-size: 116px; line-height: 1;
    letter-spacing: 2px; color: var(--ink);
  }
  .brand-domain {
    margin-top: 8px; font-weight: 400; font-size: 36px; line-height: 1.1;
    letter-spacing: 2px; color: var(--ink);
  }
  .contact-item {
    position: absolute; left: 0; right: 0;
    display: flex; flex-direction: column; align-items: center;
  }
  .contact-item.phone { top: 580px; }
  .contact-item.email { top: 690px; }
  .contact-item.address { top: 800px; }
  .contact-rule {
    position: absolute; left: 92px; right: 92px; height: 1px;
    background: var(--rule);
  }
  .contact-rule.first { top: 674px; }
  .contact-rule.second { top: 784px; }
  .contact-icon { width: 44px; height: 44px; }
  .contact-text {
    margin-top: 14px; font-size: 26px; line-height: 1.2;
    color: var(--ink-soft); white-space: nowrap;
  }
  .web-band {
    position: absolute; left: 0; right: 0; bottom: 0; height: 72px;
    background: var(--band);
    border-top: 4px solid #f2f2f2;
    display: flex; align-items: center; justify-content: center;
    font-size: 24px; color: var(--band-text); letter-spacing: 0.5px;
  }
</style>
</head>
<body>
  <main class="business-card">
    <svg class="card-shape" width="600" height="1056" viewBox="0 0 600 1056" aria-hidden="true">
      <defs>
        <linearGradient id="lower-panel" x1="0" y1="0" x2="0" y2="1">
          <stop offset="0" stop-color="#b4b3b2"/>
          <stop offset="1" stop-color="#8f8f90"/>
        </linearGradient>
      </defs>
      <polygon points="0,566 300,489 600,566 600,1056 0,1056" fill="url(#lower-panel)" opacity="0.75"/>
      <polyline points="0,566 300,489 600,566" fill="none" stroke="var(--chevron-line)" stroke-width="5"/>
    </svg>

    <header class="brand">
      <div class="brand-name-row">
        <span class="brand-mark" aria-hidden="true"></span>
        <span class="brand-name">KVTL</span>
      </div>
      <span class="brand-domain">agentur-kvtl.de</span>
    </header>

    <section class="contact-list">
      <div class="contact-item phone">
        <svg class="contact-icon" viewBox="0 0 44 44" aria-hidden="true">
          <circle cx="22" cy="22" r="20" fill="#8a8a8a" stroke="#5a5a5a" stroke-width="2"/>
          <path d="M13 19c0-3 4-5 9-5s9 2 9 5v2h-5v-2.5h-8V21h-5z" fill="#2e2e2e"/>
          <rect x="15" y="22" width="14" height="9" rx="2" fill="#2e2e2e"/>
        </svg>
        <span class="contact-text">07146-839214-0</span>
      </div>
      <div class="contact-rule first"></div>
      <div class="contact-item email">
        <svg class="contact-icon" viewBox="0 0 44 44" aria-hidden="true">
          <circle cx="22" cy="22" r="20" fill="#8a8a8a" stroke="#5a5a5a" stroke-width="2"/>
          <rect x="12" y="15" width="20" height="14" fill="#2e2e2e"/>
          <polyline points="12,15 22,23 32,15" fill="none" stroke="#8a8a8a" stroke-width="1.6"/>
        </svg>
        <span class="contact-text">Name@agentur-kvtl.de</span>
      </div>
      <div class="contact-rule second"></div>
      <div class="contact-item address">
        <svg class="contact-icon" viewBox="0 0 44 44" aria-hidden="true">
          <circle cx="22" cy="22" r="20" fill="none" stroke="#4a4a4a" stroke-width="2"/>
          <path d="M22 33c-5-6-8-10-8-14a8 8 0 0 1 16 0c0 4-3 8-8 14z" fill="none" stroke="#3a3a3a" stroke-width="2"/>
          <circle cx="22" cy="19" r="3" fill="#3a3a3a"/>
        </svg>
        <span class="contact-text">Kellberger Str. 18, 74589 Lindenhain</span>
      </div>
    </section>

    <footer class="web-band">www.agentur-kvtl.de</footer>
  </main>
</body>
</html>
```